Wellpath Ledgers New Website

Please review the attached Design Brief with additional details. Thank you!

The goal is to create a website that effectively communicates the benefits of WellPath Ledgers to eye care professionals. The website should streamline the process of understanding and utilizing WellPath Ledgers' services, emphasizing improved patient outcomes, increased referrals, and enhanced patient engagement.

Target Market(s)

Eyecare Professionals

Number of Pages Required

4 page

```html
<!DOCTYPE html>
<html lang="en">
<head>
<meta charset="utf-8">
<title>Wellpath Ledgers</title>
<link href="https://fonts.googleapis.com/css2?family=Ubuntu:wght@400;500;700&family=Lato:wght@400;700&display=swap" rel="stylesheet">
<style>
:root{
  --navy:#1b2a6b;
  --ink:#1c1f3a;
  --text:#6b6f80;
  --orange:#f8a23a;
  --blue:#3aa6e0;
  --soft:#f5f6fa;
  --dark:#2a2622;
  --footer:#151a3a;
  --footer-bar:#0f132c;
  --white:#fff;
}
*{box-sizing:border-box;margin:0;padding:0}
html,body{width:1200px;height:5220px;overflow:hidden;background:var(--white)}
body{position:relative;font-family:"Lato",sans-serif;color:var(--text)}
.abs{position:absolute}
h1,h2,h3,.heading{font-family:"Ubuntu",sans-serif}
.label{font-size:10px;font-weight:700;letter-spacing:.5px;color:var(--orange);text-transform:uppercase}
.center{text-align:center;left:0;width:1200px}
.section-title{font-size:34px;font-weight:500;color:var(--navy)}
.lead{font-size:13px;line-height:25px;color:var(--text)}
.btn{display:flex;align-items:center;justify-content:center;border-radius:22px;color:#fff;font-family:"Ubuntu",sans-serif;font-weight:500;font-size:13px;text-transform:uppercase}
.photo{position:absolute}
/* header */
.topbar-item{display:flex;gap:10px;align-items:center;font-size:11px;color:var(--ink)}
.topbar-item .dot{width:26px;height:26px;border-radius:50%;background:var(--orange);display:flex;align-items:center;justify-content:center}
.brand{font-family:"Ubuntu",sans-serif;font-weight:500;font-size:26px;color:var(--navy);display:flex;align-items:center;gap:8px}
.brand .sq{width:14px;height:14px;background:var(--orange)}
.nav a{position:absolute;top:90px;font-size:11px;color:var(--ink);text-decoration:none}
/* cards */
.feature{position:absolute;top:805px;width:318px;height:282px;background:#fff;box-shadow:0 6px 22px rgba(0,0,0,.1);text-align:center}
.feature h3{margin-top:118px;font-size:18px;font-weight:500;color:var(--navy)}
.feature p{margin:14px auto 0;width:240px;font-size:12.5px;line-height:25px}
.feature .ico{position:absolute;left:128px;top:34px;width:62px;height:62px}
.service{position:absolute;top:1928px;width:320px;height:286px}
.service .pill{position:absolute;left:60px;right:60px;bottom:-28px;height:50px;background:#fff;box-shadow:0 4px 14px rgba(0,0,0,.1);display:flex;align-items:center;justify-content:center;font-family:"Ubuntu",sans-serif;font-weight:500;font-size:15px;color:var(--navy)}
.testi{position:absolute;top:2900px;width:320px;height:265px;background:#fff;box-shadow:0 4px 18px rgba(0,0,0,.08);text-align:center}
.testi .avatar{position:absolute;left:126px;top:-32px;width:68px;height:68px;border-radius:50%;background:linear-gradient(#6d7a8c,#3c4656);border:3px solid #fff}
.testi .stars{margin-top:70px;color:#c4123c;font-size:20px;letter-spacing:6px}
.testi p{width:240px;margin:14px auto 0;font-size:12.5px;line-height:25px}
.testi .q{position:absolute;left:126px;bottom:-34px;width:68px;height:40px;border-radius:34px 34px 0 0;background:var(--orange);color:#fff;font-family:"Ubuntu",sans-serif;font-size:28px;font-weight:700;line-height:46px}
.person{position:absolute;top:3198px;width:320px;text-align:center}
.person b{display:block;font-family:"Ubuntu",sans-serif;font-weight:500;font-size:17px;color:var(--ink)}
.person span{display:block;margin-top:8px;font-size:12.5px}
.reason{position:absolute;left:140px}
.reason h4{font-family:"Ubuntu",sans-serif;font-size:12px;font-weight:500;color:var(--orange);margin-left:58px}
.reason p{margin:10px 0 0 58px;width:340px;font-size:12.5px;line-height:25px}
.field{position:absolute;height:42px;border:1.5px solid var(--navy);border-radius:22px;padding:14px 36px 0;font-size:11px;font-style:italic;color:#999}
.field span{position:absolute;top:-9px;left:30px;background:#fff;padding:0 6px;font-style:normal;font-size:12px;color:var(--navy)}
.social{width:28px;height:28px;border-radius:50%;border:1.5px solid var(--navy);display:inline-flex;align-items:center;justify-content:center;margin-right:8px}
.fsq{width:38px;height:38px;display:inline-flex;align-items:center;justify-content:center;margin-right:9px}
.finfo{position:absolute;top:5050px;display:flex;gap:14px;align-items:center;color:#fff;font-size:14px}
.finfo small{display:block;font-size:14px;color:#c9cce0}
.finfo b{font-size:14px}
</style>
</head>
<body>

<!-- Header -->
<header>
  <div class="abs topbar-item" style="left:120px;top:22px"><div class="dot"><svg width="13" height="13" viewBox="0 0 24 24"><path fill="#fff" d="M6.6 10.8a15 15 0 0 0 6.6 6.6l2.2-2.2c.3-.3.7-.4 1-.2 1.1.4 2.3.6 3.6.6.6 0 1 .4 1 1V20c0 .6-.4 1-1 1A17 17 0 0 1 3 4c0-.6.4-1 1-1h3.5c.6 0 1 .4 1 1 0 1.3.2 2.5.6 3.6.1.3 0 .7-.2 1z"/></svg></div><div><b>Call Us:</b><br>(555) 014 2290</div></div>
  <div class="abs topbar-item" style="left:280px;top:22px"><div class="dot"><svg width="13" height="13" viewBox="0 0 24 24"><path fill="#fff" d="M3 5h18v14H3zM3 6l9 7 9-7"/></svg></div><div><b>Email:</b><br>desk@wellpathledgers.test</div></div>
  <div class="abs brand" style="left:500px;top:34px"><span class="sq"></span>Wellpath Ledgers</div>
  <div class="abs btn" style="left:878px;top:16px;width:184px;height:38px;font-size:10px">Book Appointment</div>
  <div class="abs" style="left:120px;top:68px;width:942px;height:1px;background:#e6e6ee"></div>
  <nav class="nav">
    <a style="left:125px">Home</a><a style="left:235px">About Us</a><a style="left:387px">Services</a><a style="left:705px">Testimonials</a><a style="left:880px">Contact Us</a>
  </nav>
</header>

<!-- Hero -->
<section>
  <div class="photo" role="img" aria-label="Doctors reviewing documents around a desk in a bright office" style="left:0;top:126px;width:1200px;height:730px;background:linear-gradient(90deg,#2c2d33 0%,#4d5058 45%,#6d6f75 70%,#3a3b40 100%)"></div>
  <svg class="abs" style="left:0;top:700px" width="1200" height="200" viewBox="0 0 1200 200"><path d="M0 90 Q300 140 600 150 T1200 40 V200 H0Z" fill="#fff"/><path d="M1100 90 L1180 40 L1130 120 L1135 90Z" fill="var(--orange)"/></svg>
  <div class="abs" style="left:105px;top:370px;color:#fff;font-family:Ubuntu,sans-serif;font-size:19px;letter-spacing:6px;font-weight:500">EXPERTS IN</div>
  <h1 class="abs" style="left:100px;top:410px;color:#fff;font-size:48px;font-weight:500;letter-spacing:1px">WELLPATH LEDGERS</h1>
  <div class="abs" style="left:104px;top:485px;width:625px;height:2px;background:var(--orange)"></div>
  <p class="abs" style="left:104px;top:508px;width:640px;color:#fff;font-size:14.5px;line-height:28px">Lorem ipsum dolor sit amet, consectetur adipiscing elit, sed do eiusmod tempor ididunt ut labore et dolore magna aliqua</p>
  <div class="abs btn" style="left:105px;top:597px;width:146px;height:40px;background:var(--orange)">Learn More</div>
  <div class="abs btn" style="left:262px;top:597px;width:180px;height:40px;background:var(--blue)">Request Quote</div>
  <div class="abs" style="left:411px;top:910px;width:32px;height:22px;background:var(--orange)"></div>
  <div class="abs" style="left:761px;top:875px;width:27px;height:28px;background:var(--orange)"></div>

  <div class="feature" style="left:93px"><svg class="ico" viewBox="0 0 62 62"><circle cx="36" cy="36" r="22" fill="#dcefff"/><circle cx="28" cy="28" r="16" fill="none" stroke="var(--orange)" stroke-width="2"/><path d="M28 8v40M8 28h40" stroke="var(--orange)" stroke-width="2"/></svg><h3>Global Reach</h3><p>Lorem ipsum dolor sit amet, consect adipiscing elit, sed do eiusmod tempor incididunt ut labore et dolore</p></div>
  <div class="feature" style="left:443px"><svg class="ico" viewBox="0 0 62 62"><circle cx="36" cy="36" r="22" fill="#dcefff"/><rect x="14" y="16" width="28" height="26" rx="6" fill="none" stroke="var(--orange)" stroke-width="2"/><path d="M20 26h16M20 32h12" stroke="var(--orange)" stroke-width="2"/></svg><h3>Professionalism</h3><p>Lorem ipsum dolor sit amet, consect adipiscing elit, sed do eiusmod tempor incididunt ut labore et dolore</p></div>
  <div class="feature" style="left:788px"><svg class="ico" viewBox="0 0 62 62"><circle cx="36" cy="36" r="22" fill="#dcefff"/><path d="M28 12l5 10 11 2-8 8 2 11-10-5-10 5 2-11-8-8 11-2z" fill="none" stroke="var(--orange)" stroke-width="2"/></svg><h3>Continuous Innovation</h3><p>Lorem ipsum dolor sit amet, consect adipiscing elit, sed do eiusmod tempor incididunt ut labore et dolore</p></div>
</section>

<!-- Insightful data -->
<section>
  <div class="abs label" style="left:101px;top:1182px">See the difference —</div>
  <h2 class="abs" style="left:101px;top:1202px;font-size:34px;font-weight:500;color:var(--navy);line-height:53px">Insightful Data,<br>Better Outcomes</h2>
  <p class="abs" style="left:101px;top:1316px;width:415px;font-size:12.5px;line-height:25.5px">Lorem ipsum dolor sit amet, consectetur adipiscing elit, sed do eius mod tempor incididunt ut labore et dolore magna aliqua. Ut enim ad minim veniam, quis nostrud exercitation ullamco laboris nisi ut aliquip ex ea commodo consequat. Duis aute irure dolor in Lorem ipsum dolor sit amet, consectetur adipiscing elit, sed do eius mod tempor incididunt ut labore et dolore magna aliqua. Ut enim ad minim veniam, quis nostrud exercitation ullamco laboris nisi ut aliquip ex ea commodo consequat. Duis aute irure dolor in</p>
  <div class="abs btn" style="left:101px;top:1545px;width:156px;height:46px;border-radius:0;background:var(--orange);text-transform:none;font-size:15px">Contact us &nbsp;→</div>
  <svg class="abs" style="left:535px;top:1290px" width="120" height="170"><path d="M75 5 A80 80 0 0 0 75 165" fill="none" stroke="#b7dcf3" stroke-dasharray="3 4"/><path d="M80 30 A55 55 0 0 0 80 140" fill="none" stroke="#b7dcf3"/></svg>
  <div class="photo" role="img" aria-label="Nurse in blue scrubs reading a tablet" style="left:608px;top:1185px;width:497px;height:407px;border-radius:6px;background:linear-gradient(135deg,#e6eaee,#b9c7d3 55%,#7ba7c3)"></div>
  <div class="abs" style="left:580px;top:1342px;width:62px;height:62px;border-radius:50%;background:#fff;box-shadow:0 4px 14px rgba(0,0,0,.12);display:flex;align-items:center;justify-content:center"><div style="width:16px;height:16px;background:var(--orange)"></div></div>
</section>

<!-- Services -->
<section>
  <div class="abs" style="left:0;top:1665px;width:1200px;height:657px;background:var(--soft)"></div>
  <div class="abs label center" style="top:1747px">— Our Services —</div>
  <h2 class="abs section-title center" style="top:1768px">Services We Offer</h2>
  <p class="abs lead center" style="top:1832px;padding:0 300px">Lorem ipsum dolor sit amet, consectetur adipiscing elit, sed do eiusmod tempor incididunt ut labore et dolore magna aliqua. Ut enim ad minim veniam, quis nostrud exercitation</p>
  <div class="service" style="left:93px"><div class="photo" role="img" aria-label="Technician in protective gown at a lab workstation" style="inset:0;background:linear-gradient(135deg,#8c9aa6,#4f81ad)"></div><div class="pill">Health Analytics</div></div>
  <div class="service" style="left:441px"><div class="photo" role="img" aria-label="Two colleagues reviewing a laptop" style="inset:0;background:linear-gradient(135deg,#9aa0a8,#3e4048)"></div><div class="pill">Outcome Monitoring</div></div>
  <div class="service" style="left:788px"><div class="photo" role="img" aria-label="Doctor and patient looking at a tablet" style="inset:0;background:linear-gradient(135deg,#c5ccd6,#6a86a8)"></div><div class="pill">Data Management</div></div>
</section>

<!-- Call band -->
<section>
  <div class="photo" role="img" aria-label="Dark backdrop of a care team at work" style="left:0;top:2322px;width:1200px;height:306px;background:linear-gradient(90deg,#2b2622,#3a332d 50%,#241f1b)"></div>
  <h2 class="abs center heading" style="top:2432px;color:#fff;font-size:32px;font-weight:400;line-height:40px">We're On <span style="color:var(--orange)">Call 24/7</span> to React Promptly to Your<br>WellPath Ledgers Needs</h2>
  <div class="abs" style="left:347px;top:2598px;width:501px;height:52px;background:#fff;box-shadow:0 4px 16px rgba(0,0,0,.1);display:flex;align-items:center;justify-content:space-around;font-size:14px;color:var(--ink)"><span>+ (001) 555-018-240</span><span>[or]</span><span>hello@wellpathledgers.test</span></div>
</section>

<!-- Testimonials -->
<section>
  <div class="abs label center" style="top:2690px">— Testimonials —</div>
  <h2 class="abs section-title center" style="top:2710px">What clients are saying</h2>
  <p class="abs lead center" style="top:2772px;padding:0 300px">Lorem ipsum dolor sit amet, consectetur adipiscing elit, sed do eiusmod tempor incididunt ut labore et dolore magna aliqua. Ut enim ad minim veniam, quis nostrud exercitation</p>
  <div class="testi" style="left:93px"><div class="avatar" role="img" aria-label="Client portrait"></div><div class="stars">★★★★★</div><p>Lorem ipsum dolor sit amet, consectetur adipiscing elit, sed do eiusmod tempor incididunt ut labore et dolore</p><div class="q">“</div></div>
  <div class="testi" style="left:441px"><div class="avatar" role="img" aria-label="Client portrait"></div><div class="stars">★★★★★</div><p>Lorem ipsum dolor sit amet, consectetur adipiscing elit, sed do eiusmod tempor incididunt ut labore et dolore</p><div class="q">“</div></div>
  <div class="testi" style="left:788px"><div class="avatar" role="img" aria-label="Client portrait"></div><div class="stars">★★★★★</div><p>Lorem ipsum dolor sit amet, consectetur adipiscing elit, sed do eiusmod tempor incididunt ut labore et dolore</p><div class="q">“</div></div>
  <div class="person" style="left:93px"><b>Dana Whitfield</b><span>Los Angeles</span></div>
  <div class="person" style="left:441px"><b>Dana Whitfield</b><span>Los Angeles</span></div>
  <div class="person" style="left:788px"><b>Dana Whitfield</b><span>Los Angeles</span></div>
</section>

<!-- Why choose us -->
<section>
  <div class="photo" role="img" aria-label="Smiling team collaborating around laptops in an office" style="left:0;top:3297px;width:1200px;height:608px;background:linear-gradient(90deg,#3a4150,#5b5f68 45%,#4a4038 70%,#2e2a28)"></div>
  <div class="abs" style="left:92px;top:3366px;width:492px;height:469px;background:#fff;border-radius:6px"></div>
  <div class="abs label" style="left:140px;top:3424px">See the difference —</div>
  <h2 class="abs" style="left:140px;top:3446px;font-size:34px;font-weight:500;color:var(--navy)">Why Choose Us?</h2>
  <div class="reason" style="top:3520px"><svg class="abs" style="left:6px;top:4px" width="30" height="30" viewBox="0 0 30 30"><circle cx="15" cy="11" r="6" fill="none" stroke="var(--orange)" stroke-width="1.6"/><path d="M4 27c2-7 20-7 22 0" fill="none" stroke="var(--orange)" stroke-width="1.6"/></svg><h4>Customer Support</h4><p>Lorem ipsum dolor sit amet, consectetur adipiscing elit, sed do eiusmod tempor incididunt ut labore et</p></div>
  <div class="reason" style="top:3612px"><svg class="abs" style="left:6px;top:4px" width="30" height="30" viewBox="0 0 30 30"><path d="M15 3l4 8 9 1-7 6 2 9-8-5-8 5 2-9-7-6 9-1z" fill="none" stroke="var(--orange)" stroke-width="1.6"/></svg><h4>Efficient Ordering</h4><p>Lorem ipsum dolor sit amet, consectetur adipiscing elit, sed do eiusmod tempor incididunt ut labore et</p></div>
  <div class="reason" style="top:3704px"><svg class="abs" style="left:6px;top:4px" width="30" height="30" viewBox="0 0 30 30"><path d="M5 18a10 10 0 0 1 20 0" fill="none" stroke="var(--orange)" stroke-width="1.6"/><rect x="3" y="17" width="5" height="8" rx="2" fill="none" stroke="var(--orange)" stroke-width="1.6"/><rect x="22" y="17" width="5" height="8" rx="2" fill="none" stroke="var(--orange)" stroke-width="1.6"/></svg><h4>Regulatory Compliance</h4><p>Lorem ipsum dolor sit amet, consectetur adipiscing elit, sed do eiusmod tempor incididunt ut labore et</p></div>
</section>

<!-- Contact -->
<section>
  <div class="abs label center" style="top:3953px">— Contact us —</div>
  <h2 class="abs section-title center" style="top:3973px">Get In Touch With Us</h2>
  <p class="abs lead center" style="top:4036px;padding:0 300px">Lorem ipsum dolor sit amet, consectetur adipiscing elit, sed do eiusmod tempor incididunt ut labore et dolore magna aliqua. Ut enim ad minim veniam, quis nostrud exercitation</p>
  <div class="abs" style="left:140px;top:4120px;width:910px;height:478px;background:#fff;box-shadow:0 4px 24px rgba(0,0,0,.08)"></div>
  <div class="field" style="left:193px;top:4182px;width:392px;background:#dcf0fb;color:var(--navy)"><span style="background:linear-gradient(#fff 50%,#dcf0fb 50%)">Your Name</span>John</div>
  <div class="field" style="left:605px;top:4182px;width:392px"><span>Your Website</span>www.wellpath.test</div>
  <div class="field" style="left:193px;top:4256px;width:392px"><span>Your Phone</span>555 014 229</div>
  <div class="field" style="left:605px;top:4256px;width:392px"><span>Your Email</span>you@wellpath.test</div>
  <div class="field" style="left:193px;top:4330px;width:804px;height:150px;border-radius:14px"><span>Your Message</span>Type Message</div>
  <div class="abs" style="left:206px;top:4518px"><span class="social"></span><span class="social"></span><span class="social"></span><span class="social"></span></div>
  <div class="abs btn" style="left:843px;top:4510px;width:144px;height:42px;background:var(--orange);text-transform:none;font-size:12px;gap:10px">Submit Now <span style="width:22px;height:22px;border-radius:50%;background:#fff;display:inline-block"></span></div>
</section>

<!-- Footer -->
<footer>
  <div class="abs" style="left:0;top:4662px;width:1200px;height:488px;background:var(--footer)"></div>
  <div class="abs" style="left:86px;top:4774px"><span class="fsq" style="background:#3b5998"></span><span class="fsq" style="background:#0e76a8"></span><span class="fsq" style="background:#1da1f2"></span><span class="fsq" style="background:#e0102e"></span></div>
  <div class="abs brand" style="left:472px;top:4775px;color:var(--blue);font-size:36px"><span class="sq" style="width:18px;height:18px"></span>Wellpath Ledgers</div>
  <div class="abs" style="left:972px;top:4782px;color:#fff;font-size:14px;font-weight:700">Back to top</div>
  <div class="abs" style="left:1072px;top:4772px;width:42px;height:42px;background:var(--orange);display:flex;align-items:center;justify-content:center"><svg width="14" height="10"><path d="M1 8l6-6 6 6" stroke="#fff" stroke-width="2" fill="none"/></svg></div>
  <h2 class="abs center" style="top:4905px;color:#fff;font-size:25px;font-weight:500">Get free assessment today</h2>
  <p class="abs center" style="top:4950px;color:#fff;font-size:14px;line-height:26px;padding:0 310px">Lorem ipsum dolor sit amet, consectetur adipiscing elit, sed do eiusmod tempor incididunt ut labore et dolore magna aliqua.</p>
  <div class="finfo" style="left:218px"><svg width="50" height="50" viewBox="0 0 24 24"><path fill="none" stroke="var(--orange)" stroke-width="1" d="M6.6 10.8a15 15 0 0 0 6.6 6.6l2.2-2.2c.3-.3.7-.4 1-.2 1.1.4 2.3.6 3.6.6.6 0 1 .4 1 1V20c0 .6-.4 1-1 1A17 17 0 0 1 3 4c0-.6.4-1 1-1h3.5c.6 0 1 .4 1 1 0 1.3.2 2.5.6 3.6.1.3 0 .7-.2 1z"/></svg><div><small>Make a Call</small><b>+1-555-014-2290</b></div></div>
  <div class="finfo" style="left:478px"><svg width="50" height="50" viewBox="0 0 24 24"><path fill="none" stroke="var(--orange)" stroke-width="1" d="M3 6h18v13H3zM3 7l9 6 9-6"/></svg><div><small>Mail Us On</small><b>care@wellpathledgers.test</b></div></div>
  <div class="finfo" style="left:752px"><svg width="50" height="50" viewBox="0 0 24 24"><path fill="none" stroke="var(--orange)" stroke-width="1" d="M12 21s-7-7-7-12a7 7 0 0 1 14 0c0 5-7 12-7 12zM12 6.5a2.5 2.5 0 1 0 0 5 2.5 2.5 0 0 0 0-5zM3 21h18"/></svg><div><small>Location</small><b>48 Harbor Lane</b></div></div>
  <div class="abs" style="left:0;top:5150px;width:1200px;height:70px;background:var(--footer-bar)"></div>
  <div class="abs" style="left:85px;top:5184px;color:#fff;font-size:12px">Wellpath Ledgers</div>
  <div class="abs" style="left:802px;top:5184px;color:#fff;font-size:12px;word-spacing:2px">Privacy Policy &nbsp;&nbsp;&nbsp;&nbsp; Terms &amp; Conditions &nbsp;&nbsp;&nbsp;&nbsp; Site Map</div>
</footer>

</body>
</html>
```